Dwelvano - "Where Pest Control is Free for Life..." Please see pitch deck...

Project goal, that this is a reusable template, not a one-off card
Brand and design direction, follow the logo, use the brand palette (with a color swatch table), typography and layout guidance
The John Doe placeholder content as a clean field-by-field table (name, title, company, address, office, cell, fax, email, dwelvano.com)
Print specs, 3.5 × 2 in trim, 0.125 in bleed, 300 DPI, CMYK, crop marks
Deliverables, layered editable PSD (your primary ask) plus vector .AI/.EPS and a press-ready PDF/X-1a, with fonts packaged
What you'll provide (logo, colors, fonts)
Process and sign-off, concept first, then full file package on approval.
Populate every field with this John Doe placeholder data so we can see the layout fully built out. We will replace it per person.
Name John Doe
Title Title / Position
Company Dwelvano
Address 48 Harbor Lane, Suite 210, Brookfield, FL 32990
Office (904) 555-0142
Cell (904) 555-0187
Fax (904) 555-0163
Email johndoe@dwelvano.com
Website dwelvano.com

We need the working, editable source files so we can update them ourselves, plus a ready-to-print export:
1. Photoshop (.PSD) — fully layered and editable, with each contact field on its own labeled text layer. This is the primary requested format.
2. Vector source — the press-standard editable format, Adobe Illustrator (.AI) and/or .EPS, since vector is preferred for crisp text and logos at print.
3. Print-ready PDF — press-quality (PDF/X-1a), CMYK, with bleed and crop marks, both sides.
4. Packaged fonts and links — include or list all fonts used, and package any linked assets so the files open correctly on our end.

Why both PSD and vector
The PSD covers our request directly and is easy for us to edit. Vector (.AI/.EPS) is what most commercial printers actually prefer for type and logos because it stays razor-sharp at any size. Providing both keeps us flexible no matter which printer we use. Have fun and keep it modern and cool the designer of the logo did a great job, see what you can do.

```html
<!DOCTYPE html>
<html lang="en">
<head>
<meta charset="utf-8">
<title>Dwelvano Business Card Template</title>
<link href="https://fonts.googleapis.com/css2?family=Montserrat:wght@400;500;700;800&display=swap" rel="stylesheet">
<style>
  :root {
    --stage: #2a2a2c;
    --card-navy: #0a1128;
    --brand-teal: #12b4c8;
    --ink-white: #ffffff;
    --ink-soft: #e6e9ef;
  }
  * { box-sizing: border-box; margin: 0; padding: 0; }
  html, body {
    width: 1200px;
    height: 875px;
    overflow: hidden;
    background: var(--stage);
    font-family: "Montserrat", sans-serif;
  }
  .card-set {
    position: absolute;
    inset: 0;
    display: flex;
    align-items: center;
    justify-content: center;
    gap: 44px;
  }
  .card {
    position: relative;
    width: 532px;
    height: 304px;
    background: var(--card-navy);
    border-radius: 16px;
    overflow: hidden;
    box-shadow: 0 18px 40px rgba(0,0,0,.45);
  }

  /* Front */
  .card-front {
    display: flex;
    align-items: center;
    justify-content: center;
  }
  .brand-lockup {
    display: flex;
    align-items: center;
    gap: 14px;
  }
  .brand-square {
    width: 30px;
    height: 30px;
    background: var(--brand-teal);
    border-radius: 4px;
  }
  .brand-name {
    font-weight: 800;
    font-size: 66px;
    letter-spacing: -1.5px;
    color: var(--ink-white);
    line-height: 1;
  }

  /* Back */
  .accent-bar {
    position: absolute;
    top: 22px;
    right: 0;
    width: 14px;
    height: 40px;
    background: var(--brand-teal);
  }
  .person {
    position: absolute;
    top: 22px;
    right: 34px;
    text-align: right;
  }
  .person-name {
    font-weight: 700;
    font-size: 27px;
    letter-spacing: 1px;
    color: var(--brand-teal);
    line-height: 1.1;
  }
  .person-role {
    font-weight: 500;
    font-size: 15px;
    color: var(--ink-white);
    margin-top: 3px;
  }
  .back-brand {
    position: absolute;
    left: 34px;
    top: 98px;
    gap: 8px;
  }
  .back-brand .brand-square { width: 14px; height: 14px; border-radius: 2px; }
  .back-brand .brand-name { font-size: 32px; letter-spacing: -.6px; }
  .contact {
    position: absolute;
    left: 34px;
    top: 156px;
    color: var(--ink-soft);
    font-size: 12.5px;
    line-height: 1.4;
  }
  .contact-address { margin-bottom: 10px; }
  .contact-list { list-style: none; }
  .contact-list li {
    display: flex;
    align-items: center;
    gap: 8px;
  }
  .contact-icon {
    width: 11px;
    height: 11px;
    flex: none;
    fill: none;
    stroke: var(--brand-teal);
    stroke-width: 1.6;
    stroke-linecap: round;
    stroke-linejoin: round;
  }
</style>
</head>
<body>
<main class="card-set">

  <section class="card card-front" aria-label="Card front">
    <div class="brand-lockup">
      <span class="brand-square"></span>
      <span class="brand-name">Dwelvano</span>
    </div>
  </section>

  <section class="card card-back" aria-label="Card back">
    <span class="accent-bar"></span>
    <div class="person">
      <p class="person-name">JOHN DOE</p>
      <p class="person-role">Company Dwelvano</p>
    </div>

    <div class="brand-lockup back-brand">
      <span class="brand-square"></span>
      <span class="brand-name">Dwelvano</span>
    </div>

    <div class="contact">
      <p class="contact-address">48 Harbor Lane, Suite 210<br>Brookfield, FL 32990</p>
      <ul class="contact-list">
        <li>
          <svg class="contact-icon" viewBox="0 0 12 12"><path d="M2 1.5l2 .2.8 2.3-1.2.9a6 6 0 0 0 3.5 3.5l.9-1.2 2.3.8.2 2c-5 .6-9-3.4-8.5-8.5z"/></svg>
          <span>(904) 555-0142</span>
        </li>
        <li>
          <svg class="contact-icon" viewBox="0 0 12 12"><rect x="3" y="1" width="6" height="10" rx="1"/><path d="M5.5 9.2h1"/></svg>
          <span>(904) 555-0187</span>
        </li>
        <li>
          <svg class="contact-icon" viewBox="0 0 12 12"><path d="M3 4V1h6v3"/><rect x="1" y="4" width="10" height="5" rx="1"/><path d="M3 7.5h6V11H3z"/></svg>
          <span>(904) 555-0163</span>
        </li>
        <li>
          <svg class="contact-icon" viewBox="0 0 12 12"><rect x="1" y="2.5" width="10" height="7" rx="1"/><path d="M1.5 3l4.5 3.5L10.5 3"/></svg>
          <span>johndoe@dwelvano.com</span>
        </li>
        <li>
          <svg class="contact-icon" viewBox="0 0 12 12"><circle cx="6" cy="6" r="5"/><path d="M1 6h10M6 1c-2.5 3-2.5 7 0 10M6 1c2.5 3 2.5 7 0 10"/></svg>
          <span>dwelvano.com</span>
        </li>
      </ul>
    </div>
  </section>

</main>
</body>
</html>
```